Business Card for a Jewellery Brand

Business card for an upscale jewellery brand. Attached is the brand logo and icon and color board. I am looking for two card versions: one for the founder and one is generic. The card should be elegant and convey upscale and premium feel. I am open to both square and rectangle card shapes.

Industry/Entity Type

Jewelry

Contact Information for Business Card

Two cards: (1) Sunela Parvaniya (Founder) (2) General
(1) Sunela Parvaniya card should have Name: Sunela Parvaniya, Title: Founder Email id: sunela@quiremo.com.au. Phone no: +61452913307
(2) Generic card should have Email id: info@quiremo.com.au. Phone no: +61436207518

Requirements
Must have
• Workmark
• ICON
• Phone no
• Email ID
• ABN: 58219740312 (Note: ABN is Business number in Australia)
• Website: www.quiremo.com.au
• Instagram: quiremo_jewellery
• Facebook: @quiremojewellery
Nice to have
• Tagline

```html
<!DOCTYPE html>
<html lang="en">
<head>
<meta charset="utf-8">
<title>Quiremo Business Card</title>
<link href="https://fonts.googleapis.com/css2?family=Barlow+Semi+Condensed:wght@500;600&family=Roboto:wght@400&display=swap" rel="stylesheet">
<style>
  :root {
    --page-bg: #e6e6e6;
    --rose: #e38f8b;
    --rose-deep: #d98482;
    --blush: #f3d6cf;
    --text-grey: #555555;
    --marble-light: #f6f6f7;
    --marble-vein: #d9dade;
    --lamp-light: #f1d9d3;
    --lamp-mid: #dcbab3;
  }
  * { margin: 0; padding: 0; box-sizing: border-box; }
  html, body { width: 1200px; height: 960px; overflow: hidden; }
  body {
    background: var(--page-bg);
    position: relative;
    font-family: "Roboto", Arial, sans-serif;
  }
  .card {
    position: absolute;
    width: 600px;
    height: 340px;
    overflow: hidden;
  }
  .card-front { left: 302px; top: 130px; }
  .card-back { left: 300px; top: 490px; background: var(--blush); }

  .marble-surface {
    position: absolute; inset: 0;
    background:
      linear-gradient(155deg, transparent 30%, var(--marble-vein) 45%, transparent 55%),
      linear-gradient(160deg, var(--marble-light) 0%, #ececee 50%, var(--marble-light) 100%);
  }
  .brand-mark {
    position: absolute;
    left: 250px; top: 82px;
    width: 100px; height: 100px;
    border-radius: 50%;
    background: var(--rose);
  }
  .wordmark {
    position: absolute;
    left: 0; right: 0; top: 206px;
    text-align: center;
    font-family: "Barlow Semi Condensed", Arial, sans-serif;
    font-weight: 500;
    font-size: 64px;
    line-height: 64px;
    letter-spacing: 12px;
    text-indent: 12px;
    color: var(--rose);
  }

  .contact-block { position: absolute; left: 58px; top: 86px; }
  .person-name {
    font-family: "Barlow Semi Condensed", Arial, sans-serif;
    font-weight: 600;
    font-size: 22px;
    letter-spacing: 0.3px;
    color: var(--rose-deep);
    line-height: 26px;
  }
  .person-title { font-size: 16px; color: var(--text-grey); line-height: 20px; }
  .contact-list { list-style: none; margin-top: 12px; }
  .contact-list li {
    display: flex; align-items: center;
    height: 18px;
    font-size: 14px;
    color: var(--text-grey);
  }
  .contact-list svg { width: 12px; height: 12px; margin-right: 9px; flex: none; }
  .business-number { margin-top: 14px; font-size: 15px; color: var(--rose); }

  .lamp-photo {
    position: absolute; left: 320px; top: 0; width: 250px; height: 330px;
    background: radial-gradient(ellipse at 55% 65%, var(--lamp-mid) 0%, var(--lamp-light) 55%, var(--blush) 80%);
  }
</style>
</head>
<body>
  <section class="card card-front">
    <div class="marble-surface" role="img" aria-label="White marble texture with soft grey veins"></div>
    <div class="brand-mark"></div>
    <div class="wordmark">QUIREMO</div>
  </section>

  <section class="card card-back">
    <div class="contact-block">
      <h1 class="person-name">SUNELA PARVANIYA</h1>
      <p class="person-title">Founder</p>
      <ul class="contact-list">
        <li><svg viewBox="0 0 12 12"><rect x="3" y="0.5" width="6" height="11" rx="1" fill="none" stroke="#d98482" stroke-width="1.2"/><circle cx="6" cy="9.6" r="0.7" fill="#d98482"/></svg>+61452913307</li>
        <li><svg viewBox="0 0 12 12"><rect x="0.5" y="2.5" width="11" height="7.5" fill="#d98482"/><path d="M0.5 2.5 L6 7 L11.5 2.5" fill="none" stroke="#f3d6cf" stroke-width="1"/></svg>sunela@quiremo.com.au</li>
        <li><svg viewBox="0 0 12 12"><circle cx="6" cy="6" r="5.3" fill="none" stroke="#d98482" stroke-width="1.2"/><ellipse cx="6" cy="6" rx="2.3" ry="5.3" fill="none" stroke="#d98482" stroke-width="1"/><line x1="0.7" y1="6" x2="11.3" y2="6" stroke="#d98482"/></svg>www.quiremo.com.au</li>
        <li><svg viewBox="0 0 12 12"><rect x="1" y="1" width="10" height="10" rx="1.5" fill="#d98482"/></svg>quiremo_jewellery</li>
        <li><svg viewBox="0 0 12 12"><rect x="1" y="1" width="10" height="10" rx="1.5" fill="#d98482"/></svg>@quiremojewellery</li>
      </ul>
      <p class="business-number">ABN: 58219740312</p>
    </div>
    <div class="lamp-photo" role="img" aria-label="Photograph of two hanging rose-gold pendant lamps"></div>
  </section>
</body>
</html>
```